Profesional personal website needs design and business card

I need a business card with my professional name as a logo "Dorian Vitality" for my business. I am a Wellness Coach, consultant and trainer. So it should be professional, wellness oriented and modern.

Target Market(s)

Private clients, governments, corporations. Luxury and high market.

Industry/Entity Type

Health And Wellness

Contact Information for Business Card

Dorian Vitality should be the logo

Colors

Designer to choose colors to be used in the design.

Requirements
Must have
• Dorian Vitality
• Name: Tomás Lirandel
• Wellness Coach, Consultant & Trainer.
• Website: www.dorianvitality-example.com
• Phone:
• Spain (+34) 612 480 317
• (USA) +1 (555) 610 4829
Nice to have
• The most important is the design of "Dorian Vitality", as this is going to be my personal brand logo. It should be professional, wellness, high end and actual.
Should not have
• no golds, no baroque style..

```html
<!DOCTYPE html>
<html lang="en">
<head>
<meta charset="utf-8">
<title>Dorian Vitality – Business Card</title>
<link href="https://fonts.googleapis.com/css2?family=Open+Sans:wght@600;700&family=Quicksand:wght@500&display=swap" rel="stylesheet">
<style>
  :root {
    --backdrop: #0e7f8c;
    --brand-blue: #1e6bb0;
    --brand-green: #3bb23a;
    --card-white: #f1f1f1;
    --ink: #2a2a2a;
    --ink-soft: #3a3a3a;
  }
  * { margin: 0; padding: 0; box-sizing: border-box; }
  html, body {
    width: 1200px; height: 900px; overflow: hidden;
    background: var(--backdrop);
  }
  .canvas { position: relative; width: 1200px; height: 900px; }
  .card {
    position: absolute; left: 340px; width: 520px; height: 336px;
    overflow: hidden;
  }
  .card-front {
    top: 96px;
    background:
      radial-gradient(ellipse 70% 75% at 100% 100%, var(--brand-green) 0%, rgba(59,178,58,0.55) 35%, rgba(59,178,58,0) 75%),
      linear-gradient(160deg, var(--brand-blue) 0%, #2a78a8 55%, var(--brand-blue) 100%);
    display: flex; align-items: center; justify-content: center;
  }
  .front-wordmark {
    font-family: "Open Sans", sans-serif; font-weight: 700;
    font-size: 62px; color: #fff; letter-spacing: 0.5px;
    margin-top: -12px;
  }
  .card-back { top: 468px; background: var(--card-white); }
  .back-wordmark {
    position: absolute; left: 61px; top: 36px;
    font-family: "Open Sans", sans-serif; font-weight: 700;
    font-size: 46px; line-height: 1; color: var(--brand-blue);
  }
  .role {
    position: absolute; left: 63px; top: 88px;
    font-family: "Open Sans", sans-serif; font-weight: 600;
    font-size: 19px; color: var(--ink);
  }
  .contact-icon { position: absolute; left: 61px; fill: var(--brand-blue); }
  .icon-phone { top: 157px; width: 46px; height: 46px; }
  .icon-globe { top: 232px; width: 43px; height: 43px; }
  .phones {
    position: absolute; left: 125px; top: 154px;
    font-family: "Quicksand", sans-serif; font-weight: 500;
    font-size: 21px; line-height: 27px; letter-spacing: 2.2px;
    color: var(--ink-soft);
  }
  .website {
    position: absolute; left: 128px; top: 241px;
    font-family: "Quicksand", sans-serif; font-weight: 500;
    font-size: 17px; letter-spacing: 3px; color: var(--ink-soft);
  }
  .footer-band {
    position: absolute; left: 0; bottom: 0; width: 100%; height: 37px;
    background: var(--brand-blue);
  }
</style>
</head>
<body>
<main class="canvas">
  <section class="card card-front">
    <h1 class="front-wordmark">Dorian Vitality</h1>
  </section>

  <section class="card card-back">
    <h2 class="back-wordmark">Dorian Vitality</h2>
    <p class="role">Wellness Coach, Consultant &amp; Trainer</p>

    <svg class="contact-icon icon-phone" viewBox="0 0 46 46" aria-hidden="true">
      <path d="M4 10c0-4 8-7 19-7s19 3 19 7v3c0 1-1 2-2 2h-6c-1 0-2-1-2-2v-2c-3-1-6-1-9-1s-6 0-9 1v2c0 1-1 2-2 2H6c-1 0-2-1-2-2z"/>
      <path d="M16 14h4v5h6v-5h4v5c5 3 9 9 10 16 0 3-1 5-4 5H10c-3 0-4-2-4-5 1-7 5-13 10-16z"/>
      <circle cx="23" cy="29" r="6" fill="#f1f1f1"/>
      <circle cx="23" cy="29" r="3"/>
      <rect x="8" y="38" width="4" height="7" rx="2"/>
      <rect x="34" y="38" width="4" height="7" rx="2"/>
    </svg>
    <p class="phones">Spain (+34) 612 480 317<br>(USA) +1 (555) 610 4829</p>

    <svg class="contact-icon icon-globe" viewBox="0 0 44 44" aria-hidden="true">
      <g fill="none" stroke="var(--brand-blue)" stroke-width="4">
        <circle cx="22" cy="22" r="19"/>
        <ellipse cx="22" cy="22" rx="8" ry="19"/>
        <line x1="22" y1="3" x2="22" y2="41"/>
        <line x1="4" y1="16" x2="40" y2="16"/>
        <line x1="4" y1="28" x2="40" y2="28"/>
      </g>
    </svg>
    <p class="website">www.dorianvitality-example.com</p>

    <div class="footer-band"></div>
  </section>
</main>
</body>
</html>
```